Design NEW business card

We would like a business card using the colour deep red wine or dark navy blue textured background (patterned or not, open to suggestions) with a high gloss debossed rose gold/copper RM Roland Mercer Jewellery business name (Provided). I have included images for your review we would like to keep our currently logo and business name on the front but you can change the layout and positioning. For the back of the card we are open to all suggestions/variations.
Business
Use our current RM Roland Mercer Jewellery logo (Provided image)

```html
<!DOCTYPE html>
<html lang="en">
<head>
<meta charset="utf-8">
<title>Roland Mercer Jewellery – Business Cards</title>
<link rel="stylesheet" href="https://fonts.googleapis.com/css2?family=Open+Sans:wght@300;400;600&display=swap">
<style>
  :root {
    --backdrop: #3b3632;
    --wine: #5a2128;
    --wine-light: #63262e;
    --rose-gold: #c9927a;
    --rose-gold-deep: #a8705a;
    --ink-light: #f3ece8;
    --ink-muted: #cdb8b2;
  }
  * { box-sizing: border-box; margin: 0; padding: 0; }
  html, body {
    width: 1200px; height: 864px; overflow: hidden;
    background: var(--backdrop);
    font-family: "Open Sans", sans-serif;
  }
  .sheet {
    width: 1200px; height: 864px;
    display: flex; align-items: center; justify-content: center; gap: 40px;
  }
  .card {
    position: relative;
    width: 540px; height: 310px;
    background: linear-gradient(135deg, var(--wine-light), var(--wine));
    box-shadow: 0 14px 30px rgba(0,0,0,.45);
    overflow: hidden;
  }
  .monogram {
    color: var(--rose-gold);
    font-weight: 300;
    letter-spacing: 2px;
    line-height: 1;
  }
  /* front */
  .card-front .monogram {
    position: absolute; left: 60px; top: 62px; font-size: 60px;
  }
  .brand-name {
    position: absolute; left: 60px; top: 150px;
    color: var(--rose-gold-deep);
    font-weight: 300; font-size: 22px; letter-spacing: 6px;
    text-transform: uppercase;
  }
  .brand-sub {
    position: absolute; left: 62px; top: 182px;
    color: var(--rose-gold-deep);
    font-weight: 300; font-size: 11px; letter-spacing: 9px;
    text-transform: uppercase;
  }
  .front-web {
    position: absolute; left: 60px; top: 232px;
    color: var(--rose-gold-deep);
    font-size: 13px; letter-spacing: 4px;
  }
  /* back */
  .card-back .monogram {
    position: absolute; left: 44px; top: 46px; font-size: 56px;
  }
  .divider {
    position: absolute; left: 44px; right: 40px; top: 140px;
    height: 1px; background: var(--rose-gold-deep); opacity: .7;
  }
  .person {
    position: absolute; right: 36px; top: 168px; text-align: right;
  }
  .person-name {
    color: var(--rose-gold); font-weight: 600; font-size: 15px; letter-spacing: .5px;
  }
  .person-title {
    color: var(--ink-muted); font-size: 12.5px; margin-top: 1px;
  }
  .contact {
    position: absolute; right: 36px; bottom: 26px; text-align: right;
    color: var(--ink-light); font-size: 12.5px; line-height: 1.55;
  }
</style>
</head>
<body>
<main class="sheet">
  <section class="card card-front" aria-label="Card front">
    <div class="monogram">RM</div>
    <div class="brand-name">Roland Mercer</div>
    <div class="brand-sub">Jewellery</div>
    <div class="front-web">www.rmjewel.com</div>
  </section>

  <section class="card card-back" aria-label="Card back">
    <div class="monogram">RM</div>
    <div class="divider"></div>
    <div class="person">
      <div class="person-name">DANIEL HART</div>
      <div class="person-title">CEO/FOUNDER</div>
    </div>
    <div class="contact">
      <p>4120 Harbor View Road, Juneau, Alaska 99801</p>
      <p>(P) 907 555 0142 (M) 907 555 0187 (F) 907 555 0119</p>
      <p>(E) daniel@rmjewel.com (W) www.rmjewel.com</p>
    </div>
  </section>
</main>
</body>
</html>
```